Website to design and sell sundials: www.gnomonvale.com

We have a website that creates a free paper sundial, we want to migrate from this not profit free website to a website where we will continue offering the free paper sundial model but We will also offer a manufactured sundial and sell it.
In order to understand the project, please visit:
http://www.gnomonvale.com/vertical/sundial.html and
http://www.torvel.net/landing/

The website user journey should be redesigned, including the phases that are,
select language
Show product give info
Creation/edit sundial (could be one or more phases)
View created sundial
Buy sundial.

May some of them could be combined or splitted, what It have more sense.

Requirements
Must have
• A description page user journey offering freemium paper sundial and physical sundial to sell.
• A sundial creation page for "free" paper sundial
• A result page for paper sundial
• A sell page for physical

```html
<!DOCTYPE html>
<html lang="en">
<head>
<meta charset="utf-8">
<title>GnomonVale – Create your vertical sundial</title>
<link href="https://fonts.googleapis.com/css2?family=Roboto:wght@300;400;500;700&display=swap" rel="stylesheet">
<style>
:root{
  --orange:#f8ad3a;
  --red:#d3262a;
  --dark:#222222;
  --text:#444444;
  --muted:#888888;
  --line:#dcdcdc;
  --white:#ffffff;
  --blue:#1f6db3;
}
*{box-sizing:border-box;margin:0;padding:0}
html,body{width:857px;height:1200px;overflow:hidden;background:var(--white);font-family:'Roboto',sans-serif;color:var(--text)}
.page{position:relative;width:857px;height:1200px;overflow:hidden}
.abs{position:absolute}

/* header */
.brand{left:70px;top:30px;display:flex;align-items:center;gap:8px;font-size:20px;font-weight:500;color:var(--red)}
.brand-dot{width:14px;height:14px;border-radius:50%;background:var(--red)}
.social{left:480px;top:20px;display:flex;align-items:center;gap:6px;font-size:7.5px;color:#555}
.social i{display:inline-block;width:19px;height:19px;border-radius:50%}
.lang{left:709px;top:18px;width:77px;height:20px;border:1px solid var(--line);font-size:7.5px;color:#555;display:flex;align-items:center;padding-left:6px;gap:5px}
.lang .flag{width:11px;height:8px;background:#2a4d9b}
.lang .caret{margin-left:auto;margin-right:6px;font-size:7px;color:#999}
.nav{top:56px;font-size:7.5px;color:#333;font-weight:500}
.nav-active{left:406px;top:77px;width:52px;height:4px;background:var(--orange)}

/* hero */
.hero{left:0;top:81px;width:857px;height:320px;background:radial-gradient(circle at 520px 130px,#f6a21c 0,#c7660a 90px,#4a2408 200px,#0d0b0a 340px)}
.hero-kicker{left:70px;top:126px;font-size:23px;font-weight:300;color:var(--white)}
.hero-title{left:70px;top:163px;font-size:24px;font-weight:700;color:var(--white)}
.hero-copy{left:70px;top:201px;width:310px;font-size:11px;line-height:20px;font-weight:300;color:var(--white)}
.btn{background:var(--red);color:var(--white);font-size:8.5px;font-weight:500;display:flex;align-items:center;justify-content:center;border-radius:2px}
.hero-btn{left:70px;top:257px;width:95px;height:28px}
.arrow{width:20px;height:20px;border-radius:50%;background:rgba(60,60,60,.85);top:179px}

/* location */
.section-title{left:0;top:423px;width:857px;text-align:center;font-size:16px;font-weight:500;color:var(--white)}
.map{left:70px;top:468px;width:349px;height:207px;border:3px solid var(--white);background:linear-gradient(135deg,#a9c9ea 0,#cfe3c2 35%,#dfe6c6 55%,#a9c9ea 100%)}
.loc-title{left:446px;top:481px;font-size:14px;font-weight:700;color:var(--white);text-decoration:underline}
.loc-copy{left:446px;top:512px;width:340px;font-size:8.5px;line-height:18.5px;color:var(--white)}
.field{background:var(--white)}
.go{left:760px;top:586px;width:26px;height:20px;font-size:7.5px;font-weight:700}
.coord-label{top:641px;font-size:7.5px;color:var(--white)}
.coord{top:636px;height:20px;border:1px solid var(--white)}

/* options */
.opt-title{left:70px;top:761px;font-size:14px;font-weight:500;color:#333}
.panel{left:70px;top:794px;width:716px;height:259px;border:1px solid var(--line)}
.thumb{left:74px;width:180px;height:98px}
.thumb-label{left:74px;width:180px;height:25px;color:var(--white);font-size:9.5px;font-weight:500;display:flex;align-items:center;justify-content:center}
.opt-copy{left:284px;top:810px;width:490px;font-size:8.5px;line-height:18.5px;color:#555}
.lbl{left:284px;font-size:8.5px;color:#555}
.box{display:inline-block;width:7px;height:7px;border:1px solid #999;vertical-align:-1px;margin-left:2px}
.input{border:1px solid var(--line);font-size:7.5px;color:#999;display:flex;align-items:center;padding-left:10px}
.create{left:677px;top:1002px;width:95px;height:28px;font-size:8.5px}

/* footer */
.footer-head{top:1125px;font-size:10px;font-weight:500;color:var(--white)}
.footer-text{font-size:7.5px;line-height:16.5px;color:#aaa}
</style>
</head>
<body>
<div class="page">

  <!-- header -->
  <div class="abs brand"><span class="brand-dot"></span>GnomonVale</div>
  <div class="abs social">Connect with our social network :
    <i style="background:#2a5ba7"></i><i style="background:#2fa7df"></i><i style="background:#f2a51f"></i><i style="background:#1a6d8e"></i>
  </div>
  <div class="abs lang"><span class="flag"></span>Language<span class="caret">&#8964;</span></div>
  <div class="abs nav" style="left:422px">HOME</div>
  <div class="abs nav" style="left:476px">ABOUT US</div>
  <div class="abs nav" style="left:543px">SUNDIAL</div>
  <div class="abs nav" style="left:606px">OUR PRODUCT</div>
  <div class="abs nav" style="left:689px">BLOG</div>
  <div class="abs nav" style="left:739px">CONTACT US</div>
  <div class="abs nav-active"></div>

  <!-- hero -->
  <div class="abs hero" role="img" aria-label="Photo of open hands holding a glowing clock face"></div>
  <div class="abs arrow" style="left:32px"></div>
  <div class="abs arrow" style="left:803px"></div>
  <div class="abs hero-kicker">Gives you your</div>
  <div class="abs hero-title">COUNTRY'S OFFICIAL TIME</div>
  <div class="abs hero-copy">Sed ut perspiciatis unde omnis iste natus error sit voluptatem accusantium doloremque laudantium, totam...</div>
  <div class="abs btn hero-btn">READ MORE INFO</div>

  <!-- orange band with curves -->
  <svg class="abs" style="left:0;top:270px" width="857" height="470" viewBox="0 0 857 470">
    <path d="M0,13 Q170,110 420,127 Q640,130 857,12 L857,438 Q430,478 0,438 Z" fill="var(--orange)"/>
    <path d="M0,13 Q170,110 420,127 Q220,128 0,62 Z" fill="var(--red)"/>
  </svg>

  <div class="abs section-title">CREATE YOUR VERTICAL SUNDIAL</div>
  <div class="abs map" role="img" aria-label="World map for picking the sundial location"></div>
  <div class="abs loc-title">SUNDIAL LOCATION</div>
  <div class="abs loc-copy">Select the location where you want to place your paper sundial, mark a line along building wall where you want to put it. Write your address and press Go! (e.g. Pica-dilly circus, london, UK)</div>
  <div class="abs field" style="left:446px;top:586px;width:311px;height:20px"></div>
  <div class="abs btn go">GO!</div>
  <div class="abs coord-label" style="left:446px">Longitude :</div>
  <div class="abs coord" style="left:488px;width:59px"></div>
  <div class="abs coord-label" style="left:558px">Latitude :</div>
  <div class="abs coord" style="left:594px;width:59px"></div>
  <div class="abs coord-label" style="left:664px">Wall declination :</div>
  <div class="abs coord" style="left:726px;width:60px"></div>

  <!-- options -->
  <div class="abs opt-title">SUNDIAL OPTIONS</div>
  <div class="abs panel"></div>
  <div class="abs thumb" style="top:798px;background:linear-gradient(90deg,#3b3f48 0,#8c5a44 45%,#b6846a 100%)" role="img" aria-label="Paper sundial fixed on a brick wall"></div>
  <div class="abs thumb-label" style="top:896px;background:var(--orange)">WALL SUNDIAL</div>
  <div class="abs thumb" style="top:927px;background:linear-gradient(90deg,#1e1c1a 0,#6b6660 40%,#cdbba6 70%,#9aa3ad 100%)" role="img" aria-label="Paper sundial placed in a window"></div>
  <div class="abs thumb-label" style="top:1025px;background:var(--red)">WINDOW SUNDIAL</div>

  <div class="abs opt-copy">Sed ut perspiciatis unde omnis iste natus error sit voluptatem accusantium doloremque laudantium, totam rem aperiam, eaque ipsa quae ab illo inventore veritatis et quasi architecto beatae vitae dicta sunt Nemo enim ipsam voluptatem quia voluptas sit aspernatur aut odit aut fugit, sed quia consequuntur...</div>
  <div class="abs lbl" style="top:885px">Banner :</div>
  <div class="abs input" style="left:322px;top:878px;width:450px;height:24px">Paper Sundail</div>
  <div class="abs lbl" style="top:915px">Solar time :<span class="box"></span></div>
  <div class="abs lbl" style="top:933px">Civil Time :<span class="box" style="border-color:#777"></span></div>
  <div class="abs lbl" style="top:971px">Timezone :</div>
  <div class="abs input" style="left:333px;top:965px;width:439px;height:24px">(GMT+7) Bangkok, Hanoi, Jagarta<span style="margin-left:auto;margin-right:10px">&#9662;</span></div>
  <div class="abs lbl" style="top:1001px">Daylight Saving Time :<span class="box"></span></div>
  <div class="abs lbl" style="top:1019px">Equation of time :<span class="box"></span></div>
  <div class="abs btn create">CREATE SUNDIAL</div>

  <!-- footer -->
  <svg class="abs" style="left:0;top:1082px" width="857" height="118" viewBox="0 0 857 118">
    <path d="M0,0 Q430,50 857,0 L857,118 L0,118 Z" fill="var(--dark)"/>
  </svg>
  <div class="abs footer-head" style="left:70px">COPY RIGHTS</div>
  <div class="abs footer-text" style="left:70px;top:1146px">©GNOMONVALE.2016 | ALLRIGHTS RESERVED.<br>TERMS &amp; CONDITIONS</div>
  <div class="abs footer-head" style="left:290px">CONTACT</div>
  <svg class="abs" style="left:291px;top:1148px" width="16" height="20" viewBox="0 0 16 20">
    <path d="M8,19 C3,13 1,10 1,7 A7,7 0 0 1 15,7 C15,10 13,13 8,19 Z" fill="none" stroke="#999" stroke-width="1"/>
    <circle cx="8" cy="7" r="2.5" fill="none" stroke="#999"/>
  </svg>
  <div class="abs footer-text" style="left:314px;top:1146px">242,GNOMONVALECOMPANY NAME,<br>STREET NAME, CITY-9886</div>
  <svg class="abs" style="left:482px;top:1149px" width="11" height="20" viewBox="0 0 11 20">
    <rect x="0.5" y="0.5" width="10" height="19" rx="1.5" fill="none" stroke="#999"/>
    <line x1="3" y1="16" x2="8" y2="16" stroke="#999"/>
  </svg>
  <div class="abs footer-text" style="left:503px;top:1146px">PHONE:(+1010_ 5550-0199</div>
  <svg class="abs" style="left:642px;top:1149px" width="17" height="18" viewBox="0 0 17 18">
    <path d="M0.5,7 L8.5,0.8 L16.5,7 L16.5,17.5 L0.5,17.5 Z M0.5,7 L8.5,12.5 L16.5,7" fill="none" stroke="#999"/>
  </svg>
  <div class="abs footer-text" style="left:666px;top:1146px">MAIL:INFO@GNOMONVALE.COM</div>

</div>
</body>
</html>
```